Rising Together Toward Morning Glory

I need a graphic backdrop for an event . It’s a Christian concert and want to design the stage with the theme in graphics. It’s a musical concert in a closed environment. Want the graphic to be impressive and attractive to the youths . Want a white background with heavenly impressions.

We can have pictures of youths standing or praying together with a reflection of lights from above.

Am very flexible to ideas as well.

There is a logo , but it’s not compulsory to have it on the drawing now.

Target Market(s)

Undergraduates Christians

Industry/Entity Type

Event Planning

Font styles to use
Serif

Colors

Designer to choose colors to be used in the design.

Requirements
Must have
• Lights n symbol of Christ
Nice to have
• Force of lights . White background, assertive men/women standing together, taking positions of assertiveness, standing with confidence/ authority .
• It might be nice to have Jude 1:3 somewhere in the drawing because that states the theme.

```html
<!DOCTYPE html>
<html lang="en">
<head>
<meta charset="utf-8">
<title>Worship — Rising Together Toward Morning Glory</title>
<link rel="stylesheet" href="https://fonts.googleapis.com/css2?family=Cinzel:wght@900&family=Cormorant+Garamond:ital,wght@1,600&display=swap">
<style>
  :root {
    --sky-deep: #1f63d6;
    --sky-mid: #4aa6ec;
    --sky-light: #9fe0f6;
    --cloud: #f7fbfd;
    --horizon: #efe9dc;
    --earth-light: #d9a866;
    --earth-mid: #a8693a;
    --earth-dark: #6a3c24;
    --light: #ffffff;
    --glow: rgba(255,255,255,0.9);
  }
  html, body {
    margin: 0;
    padding: 0;
    width: 1200px;
    height: 800px;
    overflow: hidden;
    background: var(--light);
  }
  .backdrop {
    position: relative;
    width: 1200px;
    height: 800px;
    overflow: hidden;
    background: var(--light);
  }
  .scene-photo {
    position: absolute;
    inset: 0;
    background:
      radial-gradient(circle at 440px 130px, rgba(255,255,255,1) 0, rgba(255,255,255,0.75) 70px, rgba(255,255,255,0) 240px),
      radial-gradient(ellipse 620px 260px at 596px 400px, rgba(255,255,255,0.85) 0, rgba(255,255,255,0) 100%),
      linear-gradient(180deg,
        var(--sky-deep) 0%,
        var(--sky-mid) 20%,
        var(--sky-light) 36%,
        var(--cloud) 48%,
        var(--horizon) 57%,
        var(--earth-light) 64%,
        var(--earth-mid) 82%,
        var(--earth-dark) 100%);
  }
  .cross {
    position: absolute;
    left: 0;
    top: 0;
    filter: drop-shadow(0 0 12px var(--glow));
  }
  .title-block {
    position: absolute;
    left: 0;
    top: 372px;
    width: 1148px;
    text-align: center;
    color: var(--light);
  }
  .title {
    margin: 0;
    font-family: "Cinzel", serif;
    font-weight: 900;
    font-size: 104px;
    line-height: 1;
    letter-spacing: 1px;
    color: rgba(255,255,255,0.92);
    text-shadow: 0 0 16px rgba(255,255,255,0.6);
  }
  .theme {
    margin: 14px 0 0;
    font-family: "Cormorant Garamond", serif;
    font-style: italic;
    font-weight: 600;
    font-size: 30px;
    line-height: 1.2;
    letter-spacing: 1px;
    color: var(--light);
    text-shadow: 0 1px 8px rgba(90,50,30,0.55);
  }
</style>
</head>
<body>
  <main class="backdrop">
    <div class="scene-photo" role="img" aria-label="Photo: a young man walking away along a straight desert road toward distant mountains under a bright sky flooded with heavenly light"></div>
    <svg class="cross" width="1200" height="800" viewBox="0 0 1200 800" aria-hidden="true">
      <rect x="580" y="216" width="32" height="148" fill="rgba(255,255,255,0.95)"/>
      <rect x="512" y="272" width="168" height="32" fill="rgba(255,255,255,0.95)"/>
    </svg>
    <header class="title-block">
      <h1 class="title">WORSHIP</h1>
      <p class="theme">Rising Together Toward Morning Glory</p>
    </header>
  </main>
</body>
</html>
```